Biz Card

MARKETING today is the most rapidly changing business discipline. Media options to reach customers, actual customer preferences and consumer buying decisions change by the minute . . . no, by the second. The behavioral data generated by all aspects of the business and the new technologies that put the data to work together produce the potential to generate business intelligence and guide smart resource allocation to influence purchase and retention. However, to realize this potential, marketing professionals at all levels and in all organizations must continuously improve their skills not just from on-the-job training but by learning from masters in the field. The Bright Horizon Guild is the training center that serves this professional development need.model logos:msi.orgama.orgcontentmarketinginstitute.comBook covers on MarketingMetrics, Marketing Anaytics
Industry/Entity Type
Business
Contact Information for Business Card
Roy A. YoungCEOMarketing Science Academyphone: 310-601-4755email: roy@marketingscience.comAddress:437 South Rexford DriveBeverly Hills, CA 89377
Look and feel
Each slider illustrates characteristics of the customer's brand and the style your logo design should communicate.

```html
<!DOCTYPE html>
<html lang="en">
<head>
<meta charset="utf-8">
<title>Bright Horizon Guild – Business Card</title>
<link href="https://fonts.googleapis.com/css2?family=Open+Sans:wght@400;600;700;800&display=swap" rel="stylesheet">
<style>
  :root {
    --bg: #e9e7e4;
    --card-dark: #1d1d1f;
    --card-light: #ffffff;
    --lime: #6cc72b;
    --blue: #1f5fae;
    --ink: #2a2a2a;
    --muted: #7a7a7a;
    --emboss: #3a3a3d;
  }
  * { margin: 0; padding: 0; box-sizing: border-box; }
  html, body { width: 1200px; height: 716px; overflow: hidden; }
  body {
    background: var(--bg);
    font-family: "Open Sans", Arial, sans-serif;
    position: relative;
  }
  .card {
    position: absolute;
    top: 203px;
    width: 540px;
    height: 310px;
    border-radius: 4px;
    box-shadow: 0 6px 18px rgba(0,0,0,.18);
    overflow: hidden;
  }
  /* Front: dark side */
  .card-front { left: 45px; background: var(--card-dark); }
  .front-brand {
    position: absolute;
    top: 58px; left: 0; right: 0;
    text-align: center;
    font-weight: 800;
    font-size: 34px;
    letter-spacing: 1px;
    color: var(--emboss);
  }
  .front-band {
    position: absolute;
    top: 168px; left: 0; right: 0;
    height: 30px;
    background: var(--lime);
    display: flex; align-items: center; justify-content: center;
    font-size: 15px;
    color: #1a1a1a;
  }
  .front-url {
    position: absolute;
    top: 222px; left: 0; right: 0;
    text-align: center;
    font-size: 15px;
    color: #f2f2f2;
  }
  /* Back: white side */
  .card-back { left: 615px; background: var(--card-light); }
  .back-brand {
    position: absolute;
    top: 92px; left: 34px;
    width: 200px;
    display: flex; align-items: flex-start; gap: 10px;
  }
  .brand-square {
    width: 22px; height: 22px;
    background: var(--lime);
    flex: none;
    margin-top: 6px;
  }
  .brand-name {
    font-weight: 800;
    font-size: 30px;
    line-height: 1.05;
    color: var(--blue);
    text-transform: uppercase;
  }
  .contact {
    position: absolute;
    top: 86px; left: 286px;
    color: var(--ink);
    font-size: 14px;
    line-height: 1.45;
  }
  .contact-name { font-weight: 700; font-size: 20px; color: var(--blue); }
  .contact-role { font-size: 11px; color: var(--muted); margin-bottom: 14px; }
  .contact-line { display: flex; align-items: center; gap: 8px; }
  .contact-line svg { width: 13px; height: 13px; fill: var(--blue); flex: none; }
  .indent { padding-left: 21px; }
</style>
</head>
<body>

<section class="card card-front">
  <div class="front-brand">BRIGHT HORIZON GUILD</div>
  <div class="front-band">Executive Education in Marketing Analitics and Technology</div>
  <div class="front-url">www.brighthorizonguild.com</div>
</section>

<section class="card card-back">
  <div class="back-brand">
    <span class="brand-square"></span>
    <span class="brand-name">Bright Horizon Guild</span>
  </div>

  <div class="contact">
    <div class="contact-name">Neil P. Barton</div>
    <div class="contact-role">CEO</div>
    <div class="indent">912 North Calloway Lane</div>
    <div class="indent">Beverly Hills, CA 89377</div>
    <div class="contact-line">
      <svg viewBox="0 0 24 24" aria-hidden="true"><path d="M6.6 10.8a15.1 15.1 0 0 0 6.6 6.6l2.2-2.2a1 1 0 0 1 1-.25 11.4 11.4 0 0 0 3.6.57 1 1 0 0 1 1 1V20a1 1 0 0 1-1 1A17 17 0 0 1 3 4a1 1 0 0 1 1-1h3.5a1 1 0 0 1 1 1c0 1.25.2 2.45.57 3.57a1 1 0 0 1-.25 1z"/></svg>
      <span>310-555-0182</span>
    </div>
    <div class="contact-line">
      <svg viewBox="0 0 24 24" aria-hidden="true"><path d="M2 5h20v14H2z M2 5l10 8 10-8" fill="none" stroke="#1f5fae" stroke-width="2"/></svg>
      <span>neil@brighthorizonguild.com</span>
    </div>
  </div>
</section>

</body>
</html>
```